Professional Package for CPA Firm

We would like a stationery design for our new CPA Firm based in Atlanta, GA called 'Vale 8'. We work with investors to help grow investments, tax free. We would like the design to have a professional/minimal look with a 'wow' factor. We need 9.5″ x 4.125″, 9x12, and 10x13 mailing envelopes, business cards, and a letterhead. We have a logo that is already complete. For the letterhead, we would like to have space to put credentials at the bottom of the page

Industry/Entity Type

CPA, Accounting

```html
<!DOCTYPE html>
<html lang="en">
<head>
<meta charset="utf-8">
<title>Vale 8 — Stationery</title>
<link rel="stylesheet" href="https://fonts.googleapis.com/css2?family=Montserrat:wght@400;800&family=Open+Sans:wght@400;600;700&display=swap">
<style>
  :root {
    --bg: #e9e9e9;
    --paper: #f1f1f1;
    --ink: #1b1b1b;
    --text: #3a3a3a;
    --muted: #5a5a5a;
    --brand: #2a93c9;
    --dark: #1c1c1e;
  }
  * { margin: 0; padding: 0; box-sizing: border-box; }
  html, body { width: 1200px; height: 795px; overflow: hidden; background: var(--bg); }
  body { position: relative; font-family: "Open Sans", sans-serif; color: var(--text); }

  .sheet { position: absolute; background: var(--paper); box-shadow: 0 2px 8px rgba(0,0,0,.12); }

  .wordmark { display: flex; flex-direction: column; align-items: center; }
  .wordmark .name-row { display: flex; align-items: center; gap: 4px; }
  .wordmark .mark-square { background: var(--brand); }
  .wordmark .name { font-family: "Montserrat", sans-serif; font-weight: 800; color: var(--ink); line-height: 1; letter-spacing: .5px; }
  .wordmark .tagline { font-family: "Montserrat", sans-serif; font-weight: 400; color: var(--ink); letter-spacing: .6px; white-space: nowrap; }

  /* Letterhead */
  .letterhead { left: 292px; top: 99px; width: 293px; height: 415px; }
  .letterhead .wordmark { position: absolute; top: 58px; left: 0; right: 0; }
  .letterhead .name { font-size: 17px; }
  .letterhead .mark-square { width: 9px; height: 9px; }
  .letterhead .tagline { font-size: 5px; margin-top: 2px; }
  .letter-body { position: absolute; left: 26px; top: 98px; width: 241px; font-size: 5.4px; line-height: 8px; text-align: justify; }
  .letter-body p { margin-bottom: 8px; }
  .signature { width: 36px; height: 32px; background: #e4e4e4; border-radius: 3px; margin-top: 4px; }
  .letter-footer { position: absolute; bottom: 20px; left: 0; right: 0; text-align: center; font-size: 5.8px; line-height: 9px; color: var(--muted); }
  .contact-line { display: flex; justify-content: center; gap: 5px; align-items: center; }
  .contact-line span { display: inline-flex; align-items: center; gap: 2px; }
  .contact-line svg { width: 6px; height: 6px; fill: var(--ink); }

  /* Folder */
  .folder { left: 636px; top: 80px; width: 346px; height: 437px; }
  .folder-spine { position: absolute; left: 0; top: 0; bottom: 0; width: 18px; border-right: 1px solid #dcdcdc; }
  .folder .wordmark { position: absolute; top: 82px; left: 18px; right: 0; }
  .folder .name { font-size: 22px; }
  .folder .mark-square { width: 11px; height: 11px; }
  .folder .tagline { font-size: 6.4px; margin-top: 3px; }
  .folder-photo { position: absolute; left: 0; right: 0; top: 130px; height: 239px;
    background: linear-gradient(100deg, #3b3b3d 0%, #6a625b 28%, #b9a58a 55%, #d9a14a 72%, #2a93c9 100%); }
  .folder-url { position: absolute; left: 18px; right: 0; top: 403px; text-align: center; font-family: "Montserrat", sans-serif; font-size: 9.5px; letter-spacing: 1.6px; color: var(--ink); }
  .folder-url .domain { color: var(--brand); }

  /* Business cards */
  .card { left: 186px; width: 133px; height: 75px; }
  .card-front { top: 550px; display: flex; align-items: center; }
  .card-front .wordmark { width: 64px; }
  .card-front .name { font-size: 9px; }
  .card-front .mark-square { width: 5px; height: 5px; }
  .card-front .tagline { font-size: 2.6px; margin-top: 1px; }
  .card-divider { width: 1px; height: 36px; background: var(--brand); }
  .card-details { padding-left: 6px; font-size: 3px; line-height: 4px; color: var(--ink); }
  .card-details .person { font-weight: 700; font-size: 4.2px; line-height: 4.6px; }
  .card-details .role { font-weight: 600; margin-bottom: 3px; }
  .card-back { top: 646px; background: #3a3a3b; }

  /* Envelopes */
  .envelope { top: 561px; width: 329px; height: 157px; }
  .envelope-front { left: 353px; }
  .envelope-front .wordmark { position: absolute; left: 20px; top: 22px; width: 94px; }
  .envelope-front .name { font-size: 14px; }
  .envelope-front .mark-square { width: 7px; height: 7px; }
  .envelope-front .tagline { font-size: 4px; margin-top: 1px; }
  .envelope-front .return-address { text-align: center; font-size: 5.6px; line-height: 7px; color: var(--muted); margin-top: 3px; }
  .envelope-back { left: 713px; }
  .envelope-flap { position: absolute; left: 0; top: 0; width: 329px; height: 52px; }
  .envelope-back .wordmark { position: absolute; left: 0; right: 0; top: 20px; }
  .envelope-back .name { font-size: 9px; color: #fff; }
  .envelope-back .mark-square { width: 5px; height: 5px; }
  .envelope-back .tagline { font-size: 2.4px; color: #fff; margin-top: 1px; }
</style>
</head>
<body>

  <!-- Letterhead -->
  <section class="sheet letterhead">
    <div class="wordmark">
      <div class="name-row"><span class="mark-square"></span><span class="name">VALE 8</span></div>
      <span class="tagline">CPAs and Tax Advisors</span>
    </div>
    <div class="letter-body">
      <p>Dear customer,</p>
      <p>Lorem ipsum dolor sit amet, consectetur adipisicing elit, sed do eiusmod tempor incididunt ut labore et dolore magna aliqua. Ut enim ad minim veniam, quis nostrud exercitation ullamco laboris nisi ut aliquip ex ea commodo consequat. Duis aute irure dolor in reprehenderit in voluptate velit esse cillum dolore eu fugiat nulla pariatur. Excepteur sint occaecat cupidatat non proident, sunt in culpa qui officia deserunt mollit anim id est laborum.</p>
      <p>Lorem ipsum dolor sit amet, consectetur adipisicing elit, sed do eiusmod tempor incididunt ut labore et dolore magna aliqua. Ut enim ad minim veniam, quis nostrud exercitation ullamco laboris nisi ut aliquip ex ea commodo consequat. Duis aute irure dolor in reprehenderit in voluptate velit esse cillum dolore eu fugiat nulla pariatur. Excepteur sint occaecat cupidatat non proident, sunt in culpa qui officia deserunt mollit anim id est laborum.</p>
      <p>Lorem ipsum dolor sit amet, consectetur adipisicing elit, sed do eiusmod tempor incididunt ut labore et dolore magna aliqua. Ut enim ad minim veniam, quis nostrud exercitation ullamco laboris nisi ut aliquip ex ea commodo consequat. Duis aute irure dolor in reprehenderit in voluptate velit esse cillum dolore eu fugiat nulla pariatur. Excepteur sint occaecat cupidatat non proident, sunt in culpa qui officia deserunt mollit anim id est laborum.</p>
      <p>Lorem ipsum dolor sit amet, consectetur adipisicing elit, sed do eiusmod tempor incididunt ut labore et dolore magna aliqua. Ut enim ad minim veniam, quis nostrud exercitation ullamco laboris nisi ut aliquip ex ea commodo consequat. Duis aute irure dolor in reprehenderit.</p>
      <p style="margin-bottom:0">Yours Sincerely,</p>
      <div class="signature" role="img" aria-label="Handwritten signature"></div>
    </div>
    <footer class="letter-footer">
      <div>48 Birchwood Lane, Decatur, GA 30030</div>
      <div class="contact-line">
        <span><svg viewBox="0 0 10 10"><path d="M2 0.5l2 2-1 1.2c.6 1.3 1.6 2.3 2.9 2.9l1.2-1 2 2-1.2 1.6C4.5 9 1 5.5.6 1.7z"/></svg>+14045550172</span>
        <span><svg viewBox="0 0 10 10"><path d="M0 2h10v6H0z M0 2l5 3.5L10 2" fill="none" stroke="#1b1b1b" stroke-width="1"/></svg>info@valeeight.com</span>
        <span><svg viewBox="0 0 10 10"><circle cx="5" cy="5" r="4.3" fill="none" stroke="#1b1b1b" stroke-width="1"/><path d="M.7 5h8.6M5 .7c-2.4 2.6-2.4 6 0 8.6M5 .7c2.4 2.6 2.4 6 0 8.6" fill="none" stroke="#1b1b1b" stroke-width=".8"/></svg>www.valeeight.com</span>
      </div>
    </footer>
  </section>

  <!-- Presentation folder -->
  <section class="sheet folder">
    <div class="folder-spine"></div>
    <div class="wordmark">
      <div class="name-row"><span class="mark-square"></span><span class="name">VALE 8</span></div>
      <span class="tagline">CPAs and Tax Advisors</span>
    </div>
    <div class="folder-photo" role="img" aria-label="Photo of three advisors meeting at a table with laptops, framed by dark grey and blue diagonal panels"></div>
    <div class="folder-url">www.<span class="domain">valeeight</span>.com</div>
  </section>

  <!-- Business card front -->
  <section class="sheet card card-front">
    <div class="wordmark">
      <div class="name-row"><span class="mark-square"></span><span class="name">VALE 8</span></div>
      <span class="tagline">CPAs and Tax Advisors</span>
    </div>
    <div class="card-divider"></div>
    <div class="card-details">
      <div class="person">MARCUS ELLERY</div>
      <div class="role">Managing Director</div>
      <div>48 Birchwood Lane,</div>
      <div>Decatur, GA 30030</div>
      <div>+14045550172</div>
      <div>info@valeeight.com</div>
      <div>www.valeeight.com</div>
    </div>
  </section>

  <!-- Business card back -->
  <section class="sheet card card-back" role="img" aria-label="Dark grey repeating brand pattern with one blue accent"></section>

  <!-- Envelope front -->
  <section class="sheet envelope envelope-front">
    <div class="wordmark">
      <div class="name-row"><span class="mark-square"></span><span class="name">VALE 8</span></div>
      <span class="tagline">CPAs and Tax Advisors</span>
      <div class="return-address">48 Birchwood Lane,<br>Decatur, GA 30030</div>
    </div>
  </section>

  <!-- Envelope back -->
  <section class="sheet envelope envelope-back">
    <svg class="envelope-flap" viewBox="0 0 329 52" aria-hidden="true">
      <polygon points="0,0 329,0 322,50 7,50" fill="#1c1c1e"/>
    </svg>
    <div class="wordmark">
      <div class="name-row"><span class="mark-square"></span><span class="name">VALE 8</span></div>
      <span class="tagline">CPAs and Tax Advisors</span>
    </div>
  </section>

</body>
</html>
```